Business Card Design Project

We need a Business Card for an Mechanical Engineering firm in Singapore. The design should be Modern & Technical looking, yet eye catching.

Our company deals in Cutting Tools & Machine Accessories for the Manufacturing Industries such as Oil & Gas, Aero Space, etc... For more information on our Company, you can either email me or view our website www.torvalen.com.sg.

We are trying to revamp our image to give our consumers a fresh new perspective to our company, so we welcome all ideas.

Industry/Entity Type

Business

Requirements
Must have
• Must incorporate New Company Logo into the card as shown in Uploaded file.

```html
<!DOCTYPE html>
<html lang="en">
<head>
<meta charset="utf-8">
<title>Torvalen Tools – Business Card</title>
<link rel="stylesheet" href="https://fonts.googleapis.com/css2?family=Lato:wght@400;700&display=swap">
<style>
  :root {
    --bg: #dfe5e8;
    --card: #ffffff;
    --ink: #3a3a3a;
    --ink-soft: #555555;
    --brand: #a3193f;
    --rule: #b3213f;
    --shadow: rgba(30, 50, 60, 0.18);
  }
  * { box-sizing: border-box; margin: 0; padding: 0; }
  html, body {
    width: 1200px;
    height: 960px;
    overflow: hidden;
    background: var(--bg);
    font-family: "Lato", sans-serif;
    color: var(--ink);
  }
  .canvas {
    position: relative;
    width: 1200px;
    height: 960px;
    display: flex;
    flex-direction: column;
    align-items: center;
    justify-content: center;
    gap: 64px;
  }
  .card {
    position: relative;
    width: 630px;
    height: 360px;
    background: var(--card);
    box-shadow: 0 10px 30px var(--shadow);
  }

  /* Front */
  .card--front { display: flex; }
  .front__brand {
    width: 50%;
    display: flex;
    align-items: center;
    justify-content: center;
    gap: 12px;
  }
  .brand-dot {
    width: 22px;
    height: 22px;
    border-radius: 50%;
    background: var(--brand);
    flex: none;
  }
  .brand-name {
    font-weight: 400;
    font-size: 34px;
    letter-spacing: 1px;
    color: var(--ink);
    text-transform: uppercase;
  }
  .front__details {
    width: 50%;
    padding: 72px 34px 0 8px;
  }
  .person-name {
    font-size: 27px;
    font-weight: 400;
    letter-spacing: 0.5px;
    color: var(--ink);
  }
  .person-title {
    font-size: 17px;
    color: var(--ink-soft);
    margin-top: 4px;
  }
  .divider {
    height: 2px;
    background: var(--rule);
    margin: 14px 0 22px;
  }
  .contact-list { list-style: none; }
  .contact-item {
    display: flex;
    align-items: center;
    gap: 12px;
    font-size: 14px;
    line-height: 22px;
    color: var(--ink);
  }
  .contact-item--web { font-weight: 700; }
  .contact-icon { width: 12px; height: 12px; flex: none; fill: var(--brand); }
  .address {
    font-style: normal;
    font-size: 14px;
    line-height: 21px;
    margin-top: 18px;
    padding-left: 8px;
    color: var(--ink);
  }

  /* Back */
  .card--back {
    display: flex;
    align-items: center;
    justify-content: center;
    gap: 16px;
  }
  .card--back .brand-dot { width: 30px; height: 30px; }
  .card--back .brand-name { font-size: 46px; }
</style>
</head>
<body>
<main class="canvas">
  <section class="card card--front" aria-label="Business card front">
    <div class="front__brand">
      <span class="brand-dot" aria-hidden="true"></span>
      <span class="brand-name">Torvalen Tools</span>
    </div>
    <div class="front__details">
      <h1 class="person-name">DANIEL KOH</h1>
      <p class="person-title">Operations Director</p>
      <div class="divider"></div>
      <ul class="contact-list">
        <li class="contact-item">
          <svg class="contact-icon" viewBox="0 0 12 12" aria-hidden="true"><rect x="2.5" y="0" width="7" height="12" rx="1.2"/><rect x="4" y="1.6" width="4" height="6.5" fill="#fff"/></svg>
          65-63190427
        </li>
        <li class="contact-item">
          <svg class="contact-icon" viewBox="0 0 12 12" aria-hidden="true"><rect x="0" y="2" width="12" height="8"/><path d="M0.6 2.6 6 6.8 11.4 2.6" fill="none" stroke="#fff" stroke-width="1.2"/></svg>
          info@torvalen.com.sg
        </li>
        <li class="contact-item contact-item--web">
          <svg class="contact-icon" viewBox="0 0 12 12" aria-hidden="true"><circle cx="6" cy="6" r="6"/><path d="M0.5 6h11M6 0.5c-2.2 2.8-2.2 8.2 0 11M6 0.5c2.2 2.8 2.2 8.2 0 11" fill="none" stroke="#fff" stroke-width="0.9"/></svg>
          www.torvalen.com.sg
        </li>
      </ul>
      <address class="address">
        27 Kallang Way #05-12,<br>
        Kallang Works Hub,<br>
        Singapore 349215
      </address>
    </div>
  </section>

  <section class="card card--back" aria-label="Business card back">
    <span class="brand-dot" aria-hidden="true"></span>
    <span class="brand-name">Torvalen Tools</span>
  </section>
</main>
</body>
</html>
```